Falkrin homes and renovations business card design.

Would like some new card designs utilizing my new logo that look professional. I am open to different colors on the logo or utilize the same ones we have. I like the original concept but would like to see some fresh ideas and build on what we have already done.

Target Market(s)

Custom home building industry, Real estate sales, Renovation projects.

Industry/Entity Type

Home Builder

Contact Information for Business Card

Falkrin Homes and Renovations
2871 96th Avenue
Corvell, Westmark
T2R3W8
Home : 403- 718-4063 Cell: 403- 294-5170

My info is : Dax Falkrin, President and CEO
email: falkrinhomes@maildrop-example.net
Website: falkrinhomes-example.com
websit

Requirements
Must have
• Must Use my new logo design. I am open to different colors on the logo or utilize the same ones in the existing design. I can upload the original logo design if needed.

```html
<!DOCTYPE html>
<html lang="en">
<head>
<meta charset="utf-8">
<title>Falkrin Homes and Renovations – Business Card</title>
<link href="https://fonts.googleapis.com/css2?family=Montserrat:wght@400;500;600;700&display=swap" rel="stylesheet">
<style>
  :root {
    --stage: #ece9e4;
    --charcoal: #231f20;
    --charcoal-soft: #3a3536;
    --paper: #ffffff;
    --gold: #f4b71c;
    --gold-deep: #c8962a;
    --bronze: #a8752a;
    --grey: #8a8a8a;
    --ink-light: #e8e6e3;
  }
  * { margin: 0; padding: 0; box-sizing: border-box; }
  html, body { width: 1200px; height: 675px; overflow: hidden; }
  body {
    background: var(--stage);
    font-family: "Montserrat", sans-serif;
    position: relative;
  }
  .card {
    position: absolute;
    top: 195px;
    width: 500px;
    height: 286px;
    box-shadow: 0 10px 28px rgba(0,0,0,0.18);
    overflow: hidden;
  }
  .card-back {
    left: 70px;
    background: linear-gradient(160deg, var(--charcoal-soft), var(--charcoal) 60%, #151213);
    display: flex;
    align-items: center;
    justify-content: center;
  }
  .card-front { left: 630px; background: var(--paper); }
  .card-front .wave { position: absolute; inset: 0; width: 100%; height: 100%; }

  .wordmark {
    font-weight: 600;
    text-transform: uppercase;
    line-height: 1;
  }
  .wordmark .name { display: block; letter-spacing: 1px; }
  .wordmark .tagline { display: block; letter-spacing: 1.2px; margin-top: 6px; }
  .card-back .wordmark { color: var(--gold-deep); text-align: center; }
  .card-back .wordmark .name { font-size: 54px; }
  .card-back .wordmark .tagline { font-size: 15.5px; }

  .card-front .wordmark {
    position: absolute;
    left: 34px;
    top: 118px;
    color: var(--bronze);
  }
  .card-front .wordmark .name { font-size: 40px; }
  .card-front .wordmark .tagline { font-size: 11.4px; }

  .holder {
    position: absolute;
    right: 30px;
    top: 28px;
    text-align: right;
  }
  .holder-name { color: var(--gold); font-weight: 700; font-size: 22px; }
  .holder-title { color: var(--grey); font-size: 9.5px; font-weight: 500; margin-top: 2px; }

  .contact {
    position: absolute;
    right: 30px;
    top: 152px;
    text-align: right;
    color: var(--ink-light);
    font-size: 7.5px;
    line-height: 1.5;
  }
  .contact .address { margin-bottom: 8px; }
  .contact-line { display: flex; justify-content: flex-end; align-items: center; gap: 5px; }
  .contact-line svg { width: 8px; height: 8px; flex: none; }
</style>
</head>
<body>
  <section class="card card-back" aria-label="Business card, back">
    <div class="wordmark">
      <span class="name">Falkrin</span>
      <span class="tagline">Homes and Renovations</span>
    </div>
  </section>

  <section class="card card-front" aria-label="Business card, front">
    <svg class="wave" viewBox="0 0 500 286" preserveAspectRatio="none" aria-hidden="true">
      <path d="M258,0 C218,50 218,100 258,140 C298,180 303,232 273,286 L500,286 L500,0 Z" fill="var(--gold)"/>
      <path d="M266,0 C226,50 226,100 266,140 C306,180 311,232 281,286 L500,286 L500,0 Z" fill="var(--paper)"/>
      <path d="M272,0 C232,50 232,100 272,140 C312,180 317,232 287,286 L500,286 L500,0 Z" fill="var(--charcoal)"/>
    </svg>

    <div class="wordmark">
      <span class="name">Falkrin</span>
      <span class="tagline">Homes and Renovations</span>
    </div>

    <div class="holder">
      <div class="holder-name">Dax Falkrin</div>
      <div class="holder-title">President and CEO</div>
    </div>

    <div class="contact">
      <div class="address">2871 96th Avenue<br>Corvell, Westmark<br>T2R3W8</div>
      <div class="contact-line">403- 718-4063
        <svg viewBox="0 0 8 8" aria-hidden="true"><rect x="2" y="0.5" width="4" height="7" rx="0.8" fill="none" stroke="currentColor" stroke-width="0.9"/></svg>
      </div>
      <div class="contact-line">403- 294-5170
        <svg viewBox="0 0 8 8" aria-hidden="true"><path d="M1,3 Q4,0.5 7,3 L6,4 L5,3.4 L3,3.4 L2,4 Z M1.8,5 H6.2 V7.2 H1.8 Z" fill="currentColor"/></svg>
      </div>
      <div class="contact-line">falkrinhomes@maildrop-example.net
        <svg viewBox="0 0 8 8" aria-hidden="true"><rect x="0.5" y="1.5" width="7" height="5" fill="currentColor"/><path d="M0.5,1.5 L4,4.3 L7.5,1.5" fill="none" stroke="var(--charcoal)" stroke-width="0.7"/></svg>
      </div>
      <div class="contact-line">falkrinhomes-example.com
        <svg viewBox="0 0 8 8" aria-hidden="true"><circle cx="4" cy="4" r="3.4" fill="none" stroke="currentColor" stroke-width="0.9"/><path d="M0.6,4 H7.4 M4,0.6 V7.4" stroke="currentColor" stroke-width="0.6"/></svg>
      </div>
    </div>
  </section>
</body>
</html>
```